Company website for an international IT business

We require a website for our business, Korvel Solutions. The business has two primary areas: Lanterns, which includes two machine learning/deep learning based products and IT consultancy, which is the service we provide to other businesses.

We bridge cutting-edge research to market.

STYLING:
The site can be on single page or multi-page. This is fully open to suggestion. So long as the look and feel are consistent. Currently, we have no strong preference for colors, styles or layouts.
You can find the logo of our website in the attachment “Korvel-logo.png” and “Korvel-logo-landscape.png”.

CONTENT:
You can find the text of the website in “Website-Content.pdf”, which explains the services and products of our business. The format of the text is also open to suggestion - including breaking up the text into visually appealing sections.
We would also like to include suitable images on the website so that it does not appear to be a text-heavy page. We are happy to have placeholder images on stock image sites if needed. We are open to suggestions on placing of images

ATTACHMENT:

Industry/Entity Type

It Company

Coding

Coded - Design and coding required

Number of Pages Required

1 page

Colors

Designer to choose colors to be used in the design.

Requirements
Must have
• A full description of the requirement is in the attachment "Website-Content.pdf"
• The design must have HTML/CSS, and all resources relevant (images, fonts etc)
• We are
Nice to have
• We are open to suggestions on top of the requirement, please reach out and communicate.

```html
<!DOCTYPE html>
<html lang="en">
<head>
<meta charset="utf-8">
<title>Korvel Solutions</title>
<link rel="stylesheet" href="https://fonts.googleapis.com/css2?family=ABeeZee&family=Roboto:wght@400;500;700&display=swap">
<style>
:root{
  --blue:#0b7fc1;
  --blue-bright:#1a8fd3;
  --blue-deep:#0a6fae;
  --ink:#333333;
  --text:#555555;
  --muted:#777777;
  --grey-band:#ececec;
  --dark:#333333;
  --darker:#262626;
  --white:#ffffff;
}
*{margin:0;padding:0;box-sizing:border-box}
html,body{width:1200px;height:3629px;overflow:hidden}
body{font-family:"Roboto",sans-serif;color:var(--text);background:var(--white);position:relative}
.section{position:absolute;left:0;width:1200px}
.heading{font-family:"ABeeZee",sans-serif;font-weight:400;color:var(--blue);text-align:center;font-size:38px;position:absolute;left:0;width:1200px}

/* hero */
.hero{top:0;height:605px;background:linear-gradient(180deg,#e9ecef 0%,#dfe3e7 55%,#f3f4f5 100%)}
.hero-photo{position:absolute;inset:0;background:linear-gradient(100deg,#cfd5db 0%,#e4e7ea 40%,#eef0f2 60%,#c9cfd6 100%);opacity:.9}
.brand-mark{position:absolute;left:491px;top:145px;width:218px;height:218px;border-radius:50%;background:var(--blue)}
.brand-name{position:absolute;left:0;width:1200px;top:410px;text-align:center;font-family:"ABeeZee",sans-serif;font-size:68px;letter-spacing:10px;color:#2b2b2b}

/* nav */
.nav{top:605px;height:51px;background:var(--blue);display:flex;align-items:stretch}
.nav-list{display:flex;list-style:none;margin-left:77px}
.nav-list li{color:var(--white);font-size:16px;padding:0 18px;display:flex;align-items:center;letter-spacing:.3px}
.nav-list li.active{background:var(--dark);padding:0 26px}
.nav-cta{margin-left:auto;width:244px;background:var(--dark);color:var(--white);font-size:21px;display:flex;align-items:center;justify-content:center;letter-spacing:.5px}

/* welcome */
.welcome{top:656px;height:605px}
.welcome .heading{top:52px}
.lead{position:absolute;left:0;width:1200px;text-align:center;font-size:15px;line-height:27px;color:var(--text)}
.service-photo{position:absolute;top:198px;width:325px;height:199px}
.service-line{position:absolute;left:77px;top:455px;width:1046px;height:2px;background:#9ec9e4}
.service-icon{position:absolute;top:436px;width:44px;height:40px;background:var(--white);display:flex;align-items:center;justify-content:center}
.service-label{position:absolute;top:508px;width:325px;text-align:center;font-size:20px;color:var(--ink);letter-spacing:.3px}

/* different */
.different{top:1261px;height:292px;background:var(--grey-band)}
.different .heading{top:44px}
.different p{position:absolute;left:240px;width:720px;text-align:center;font-size:14px;line-height:24px;color:var(--muted)}

/* agile */
.agile{top:1553px;height:448px;background:linear-gradient(90deg,#2f8fcc 0%,#3a9ad6 50%,#1f82c4 100%);overflow:hidden}
.agile-heading{position:absolute;top:52px;left:0;width:1200px;text-align:center;font-family:"ABeeZee",sans-serif;font-size:40px;color:var(--white)}
.step{position:absolute;left:77px;width:167px;height:56px;background:var(--white);font-size:18px;color:var(--ink);display:flex;align-items:center;padding-left:14px}
.step b{color:var(--blue);font-weight:500;margin-right:14px}
.step.current::after{content:"";position:absolute;right:-16px;top:12px;border-left:16px solid var(--white);border-top:16px solid transparent;border-bottom:16px solid transparent}
.agile-copy{position:absolute;left:278px;top:156px;width:360px;font-size:14.5px;line-height:26px;color:var(--white)}
.agile-copy p+p{margin-top:4px}
.agile-photo{position:absolute;left:680px;top:153px;width:445px;height:295px}

/* help */
.help{top:2001px;height:388px}
.help .heading{top:42px}
.help-circle{position:absolute;top:131px;width:122px;height:122px;border-radius:50%;border:6px solid var(--blue);display:flex;align-items:center;justify-content:center}
.help-text{position:absolute;top:276px;width:300px;text-align:center;font-size:14px;line-height:27px;color:var(--text)}

/* statement */
.statement{top:2389px;height:145px;background:var(--blue);color:var(--white);text-align:center;font-family:"ABeeZee",sans-serif;font-size:23px;line-height:36px;padding-top:37px}

/* blog */
.blog{top:2534px;height:648px}
.blog .heading{top:50px}
.post{position:absolute;top:121px;width:325px}
.post-photo{width:325px;height:218px}
.post-meta{display:flex;justify-content:space-between;margin-top:26px;font-size:15px;color:var(--text)}
.post-meta span{display:flex;align-items:center;gap:10px}
.post-title{margin-top:14px;font-size:19px;line-height:31px;font-weight:500;color:var(--ink)}
.post-body{margin-top:8px;font-size:14.5px;line-height:25px;color:var(--text)}
.read-more{margin-top:14px;font-size:14px;font-weight:700;color:var(--blue);display:flex;align-items:center;gap:14px;text-decoration:underline}

/* signup */
.signup{top:3182px;height:104px;background:var(--blue-bright);display:flex;align-items:center}
.signup-text{margin-left:79px;font-family:"ABeeZee",sans-serif;font-size:22px;color:var(--white)}
.signup-field{position:absolute;left:694px;top:32px;width:292px;height:42px;background:var(--white);font-size:15px;color:#666;display:flex;align-items:center;padding-left:14px}
.signup-button{position:absolute;left:994px;top:32px;width:128px;height:42px;background:#0d78ba;color:var(--white);font-size:17px;display:flex;align-items:center;justify-content:center;letter-spacing:.3px}

/* footer */
.footer{top:3286px;height:291px;background:var(--dark)}
.footer-mark{position:absolute;left:99px;top:45px;width:108px;height:108px;border-radius:50%;background:var(--blue-bright)}
.footer-name{position:absolute;left:78px;top:164px;font-family:"ABeeZee",sans-serif;font-size:30px;letter-spacing:4px;color:var(--white)}
.social{position:absolute;top:218px;width:44px;height:44px;border-radius:50%;background:var(--white);border:3px solid #555}
.contact-item{position:absolute;left:836px;display:flex;gap:18px;color:var(--white);font-size:15px;line-height:27px;width:300px}
.contact-item svg{flex:none;margin-top:5px}
.copyright{top:3577px;height:52px;background:var(--darker);color:#ddd;font-size:14px;display:flex;align-items:center;justify-content:center}
</style>
</head>
<body>

<header class="section hero">
  <div class="hero-photo" role="img" aria-label="Soft hazy photo of a city skyline and hands typing on a laptop"></div>
  <div class="brand-mark"></div>
  <div class="brand-name">KORVEL</div>
</header>

<nav class="section nav">
  <ul class="nav-list">
    <li class="active">HOME</li>
    <li>ABOUT</li>
    <li>LANTERNS</li>
    <li>CONSULTANCY</li>
    <li>CONTACT</li>
  </ul>
  <div class="nav-cta">CONTACT US</div>
</nav>

<section class="section welcome">
  <h1 class="heading">Welcome to Korvel Solutions</h1>
  <p class="lead" style="top:103px">Korvel Solutions is an IT consultancy firm with a difference<br>We can provide IT expertise for your business at any stage - from initial idea to live systems</p>

  <div class="service-photo" style="left:77px;background:linear-gradient(135deg,#1c2330,#2f3c52 60%,#56657a)" role="img" aria-label="Photo of a laptop showing code on a dark desk"></div>
  <div class="service-photo" style="left:438px;background:linear-gradient(135deg,#3d7f91,#5aa3b3 50%,#2c6577)" role="img" aria-label="Photo of a circuit board with glowing network overlay"></div>
  <div class="service-photo" style="left:798px;background:linear-gradient(135deg,#6c8fb4,#a9c6e2 55%,#5f7fa3)" role="img" aria-label="Photo of a hand touching floating technology icons"></div>

  <div class="service-line"></div>
  <div class="service-icon" style="left:218px"><svg width="28" height="22" viewBox="0 0 28 22" fill="none" stroke="#0b7fc1" stroke-width="2"><rect x="2" y="2" width="24" height="18" rx="2"/><path d="M2 7h24M10 12l-3 2 3 2M18 12l3 2-3 2"/></svg></div>
  <div class="service-icon" style="left:578px"><svg width="30" height="24" viewBox="0 0 30 24" fill="none" stroke="#0b7fc1" stroke-width="2"><circle cx="15" cy="7" r="4"/><path d="M15 11v5M4 20h22M8 16h14M4 20l4-4M26 20l-4-4"/></svg></div>
  <div class="service-icon" style="left:939px"><svg width="24" height="28" viewBox="0 0 24 28" fill="none" stroke="#0b7fc1" stroke-width="2"><path d="M12 2a9 9 0 0 1 9 9c0 4-3 5-3 8v3H8v-3c0-3-4-4-4-8a8 8 0 0 1 8-9z"/><path d="M9 26h6"/></svg></div>

  <div class="service-label" style="left:77px">Software development</div>
  <div class="service-label" style="left:438px">IOT System Design</div>
  <div class="service-label" style="left:798px">Machine learning solutions</div>
</section>

<section class="section different">
  <h2 class="heading">How are we different</h2>
  <p style="top:106px">Lorem Ipsum is simply dummy text of the printing and typesetting industry. Lorem Ipsum has been the industry's standard dummy text ever since the 1500s, when an unknown printer took a galley of type and scrambled it to make a type specimen book.</p>
  <p style="top:190px">Lorem Ipsum is simply dummy text of the printing and typesetting industry. Lorem Ipsum has been the industry's standard dummy text ever since the 1500s, when an unknown printer.</p>
</section>

<section class="section agile">
  <h2 class="agile-heading">Iterative Agile Process</h2>
  <div class="step current" style="top:160px"><b>01.</b>Define</div>
  <div class="step" style="top:238px"><b>02.</b>Build</div>
  <div class="step" style="top:318px"><b>03.</b>Deliver</div>
  <div class="agile-copy">
    <p>Our conversation will start with a high-level agreement on the overall strategy.</p>
    <p>Our tech team will research and investigate the context of the work. This includes understanding of your product and your business needs.</p>
    <p>We agree on a clear definition of deliverables which are broken down to multiple milestones</p>
    <p>No commitment needed for this stage</p>
  </div>
  <div class="agile-photo" style="background:linear-gradient(160deg,#2d3a48 0%,#5b7389 45%,#c9d6e2 100%)" role="img" aria-label="Photo of hands holding a tablet showing a business team meeting"></div>
</section>

<section class="section help">
  <h2 class="heading">How can we help</h2>
  <div class="help-circle" style="left:176px"><svg width="46" height="46" viewBox="0 0 46 46" fill="none" stroke="#333" stroke-width="2.4"><circle cx="25" cy="26" r="14"/><path d="M25 26l6-6M22 8h6M25 8v4M4 22h6M2 28h7M5 34h6"/></svg></div>
  <div class="help-circle" style="left:539px"><svg width="40" height="48" viewBox="0 0 40 48" fill="none" stroke="#333" stroke-width="2.4"><path d="M14 4h12l-4 8h-4z"/><path d="M18 12C6 18 4 28 6 36c2 7 26 7 28 0 2-8 0-18-12-24"/><path d="M23 22c-2-2-7-1-6 2s7 2 7 5-5 4-7 2M20 19v3M20 31v3"/></svg></div>
  <div class="help-circle" style="left:900px"><svg width="50" height="34" viewBox="0 0 50 34" fill="none" stroke="#333" stroke-width="2.4"><path d="M2 17h8l3-8 4 18 4-24 4 30 4-26 4 20 3-10h12"/></svg></div>
  <div class="help-text" style="left:87px">Acquire more development capacity<br>and get results fast</div>
  <div class="help-text" style="left:450px">Avoid the overhead incurred by frequent<br>scaling of your development team</div>
  <div class="help-text" style="left:811px">Reach a wide spectrum of expertise</div>
</section>

<section class="section statement">
  We have many years experience in machine learning, data mining, app development,<br>DevOps and hardware design We solve “hard” problems for business
</section>

<section class="section blog">
  <h2 class="heading">Latest Blog</h2>

  <article class="post" style="left:77px">
    <div class="post-photo" style="background:linear-gradient(180deg,#c6cfd8 0%,#6e747c 55%,#2c2a2a 100%)" role="img" aria-label="Photo of business people silhouetted against an office window"></div>
    <div class="post-meta"><span><svg width="16" height="16" viewBox="0 0 16 16" fill="none" stroke="#0b7fc1" stroke-width="1.6"><rect x="1.5" y="3" width="13" height="11.5"/><path d="M1.5 7h13M5 1v4M11 1v4"/></svg>05 May 2017</span><span><svg width="16" height="16" viewBox="0 0 16 16" fill="#0b7fc1"><path d="M11 1l4 4-9 9H2v-4z"/></svg>By Admin</span></div>
    <h3 class="post-title">Lorem Ipsum is simply dummy text of the printing.</h3>
    <p class="post-body">Lorem Ipsum is simply dummy text of the printing and typesetting industry. Lorem Ipsum has been the industry's standard.</p>
    <div class="read-more">READ MORE <svg width="16" height="12" viewBox="0 0 16 12" fill="none" stroke="#0b7fc1" stroke-width="2.2"><path d="M2 1l5 5-5 5M9 1l5 5-5 5"/></svg></div>
  </article>

  <article class="post" style="left:438px">
    <div class="post-photo" style="background:linear-gradient(160deg,#e8eef4 0%,#8aa6c4 45%,#2e3f5a 100%)" role="img" aria-label="Photo of a businessman in a suit working with documents"></div>
    <div class="post-meta"><span><svg width="16" height="16" viewBox="0 0 16 16" fill="none" stroke="#0b7fc1" stroke-width="1.6"><rect x="1.5" y="3" width="13" height="11.5"/><path d="M1.5 7h13M5 1v4M11 1v4"/></svg>05 May 2017</span><span><svg width="16" height="16" viewBox="0 0 16 16" fill="#0b7fc1"><path d="M11 1l4 4-9 9H2v-4z"/></svg>By Admin</span></div>
    <h3 class="post-title">Lorem Ipsum is simply dummy text of the printing.</h3>
    <p class="post-body">Lorem Ipsum is simply dummy text of the printing and typesetting industry. Lorem Ipsum has been the industry's standard.</p>
    <div class="read-more">READ MORE <svg width="16" height="12" viewBox="0 0 16 12" fill="none" stroke="#0b7fc1" stroke-width="2.2"><path d="M2 1l5 5-5 5M9 1l5 5-5 5"/></svg></div>
  </article>

  <article class="post" style="left:798px">
    <div class="post-photo" style="background:linear-gradient(150deg,#dfe4ea 0%,#9fa9b5 50%,#3c4656 100%)" role="img" aria-label="Photo of a business team discussing work at a table"></div>
    <div class="post-meta"><span><svg width="16" height="16" viewBox="0 0 16 16" fill="none" stroke="#0b7fc1" stroke-width="1.6"><rect x="1.5" y="3" width="13" height="11.5"/><path d="M1.5 7h13M5 1v4M11 1v4"/></svg>05 May 2017</span><span><svg width="16" height="16" viewBox="0 0 16 16" fill="#0b7fc1"><path d="M11 1l4 4-9 9H2v-4z"/></svg>By Admin</span></div>
    <h3 class="post-title">Lorem Ipsum is simply dummy text of the printing.</h3>
    <p class="post-body">Lorem Ipsum is simply dummy text of the printing and typesetting industry. Lorem Ipsum has been the industry's standard.</p>
    <div class="read-more">READ MORE <svg width="16" height="12" viewBox="0 0 16 12" fill="none" stroke="#0b7fc1" stroke-width="2.2"><path d="M2 1l5 5-5 5M9 1l5 5-5 5"/></svg></div>
  </article>
</section>

<section class="section signup">
  <div class="signup-text">To get latest updates and promotions signup now!</div>
  <div class="signup-field">Enter Your Email</div>
  <div class="signup-button">SUBSCRIBE</div>
</section>

<footer class="section footer">
  <div class="footer-mark"></div>
  <div class="footer-name">KORVEL</div>
  <div class="social" style="left:80px"></div>
  <div class="social" style="left:130px"></div>
  <div class="social" style="left:180px"></div>

  <div class="contact-item" style="top:76px"><svg width="16" height="20" viewBox="0 0 16 20" fill="#fff"><path d="M8 0a7 7 0 0 1 7 7c0 5-7 13-7 13S1 12 1 7a7 7 0 0 1 7-7zm0 4a3 3 0 1 0 0 6 3 3 0 0 0 0-6z"/></svg><span>Lorem Ipsum is simply dummy text of the printing and typesetting industry.</span></div>
  <div class="contact-item" style="top:170px"><svg width="16" height="16" viewBox="0 0 16 16" fill="#fff"><path d="M3 0l3 4-2 2c1 2 4 5 6 6l2-2 4 3-2 3C7 16 0 9 0 3z"/></svg><span>555 014 2270</span></div>
  <div class="contact-item" style="top:206px"><svg width="17" height="13" viewBox="0 0 17 13" fill="none" stroke="#fff" stroke-width="1.6"><rect x="1" y="1" width="15" height="11"/><path d="M1 1l7.5 6L16 1"/></svg><span>info@korvelsolutions.com</span></div>
</footer>

<div class="section copyright">2018 ©KORVEL. All Rights Reserved.</div>

</body>
</html>
```